KDWB Business Card

Looking for a business card design to incorporate our branding. We want to only use the colors listing in the Branding Package (attached).
Updates

Target Market(s)

People who need their phone or device fixed.

Industry/Entity Type

Electronics

Contact Information for Business Card

Please use:

Brightwick Gadget Clinic LLC
4810 E Harlow Ridge Rd
Suite 417
San Antonio, TX 78163

Marcus Delgrove, Store Manager

(210) 555-0147

Requirements
Must have
• Must include the colors that are contained within the Branding Package PDF file.

```html
<!DOCTYPE html>
<html lang="en">
<head>
<meta charset="utf-8">
<title>Brightwick Gadget Clinic – Business Card</title>
<link rel="stylesheet" href="https://fonts.googleapis.com/css2?family=Arimo:wght@400;700&display=swap">
<style>
  :root {
    --backdrop: #3a3532;
    --card: #161616;
    --card-edge: #222222;
    --orange: #f05a22;
    --white: #ffffff;
    --grey: #bdbdbd;
  }
  * { margin: 0; padding: 0; box-sizing: border-box; }
  html, body { width: 1200px; height: 764px; overflow: hidden; }
  body {
    background: var(--backdrop);
    font-family: "Arimo", Arial, sans-serif;
    position: relative;
  }
  .card {
    position: absolute;
    top: 228px;
    width: 540px;
    height: 309px;
    background: var(--card);
    border: 1px solid var(--card-edge);
    border-radius: 3px;
    box-shadow: 0 10px 26px rgba(0,0,0,.45);
    overflow: hidden;
  }
  .card--front { left: 40px; }
  .card--back { left: 620px; }

  .brand {
    position: absolute;
    display: flex;
    align-items: center;
    gap: 12px;
  }
  .brand__mark {
    width: 34px; height: 34px;
    background: var(--orange);
    border-radius: 6px;
    flex: none;
  }
  .brand__name {
    color: var(--orange);
    font-size: 22px;
    font-weight: 400;
    letter-spacing: .3px;
    white-space: nowrap;
  }
  .card--front .brand { left: 118px; top: 66px; }
  .card--back .brand { left: 50%; top: 50%; transform: translate(-50%, -50%); }

  .person {
    position: absolute;
    left: 68px;
    top: 166px;
    text-align: right;
    width: 150px;
  }
  .person__name { color: var(--white); font-size: 17px; }
  .person__role { color: var(--orange); font-size: 10px; margin-top: 3px; }

  .divider {
    position: absolute;
    left: 236px; top: 142px;
    width: 1px; height: 72px;
    background: var(--white);
  }

  .contact {
    position: absolute;
    left: 252px; top: 150px;
    list-style: none;
  }
  .contact__item {
    display: flex;
    align-items: center;
    gap: 8px;
    color: var(--white);
    font-size: 11px;
    height: 18px;
  }
  .contact__icon {
    width: 11px; height: 11px;
    background: var(--orange);
    flex: none;
    display: block;
  }

  .address-band {
    position: absolute;
    left: 0; right: 0; bottom: 0;
    height: 60px;
    background: var(--orange);
    color: var(--white);
    font-size: 15px;
    display: flex;
    align-items: center;
    padding-left: 70px;
    letter-spacing: .2px;
  }
</style>
</head>
<body>
  <section class="card card--front" aria-label="Business card front">
    <div class="brand">
      <span class="brand__mark"></span>
      <span class="brand__name">Brightwick Gadget Clinic</span>
    </div>

    <div class="person">
      <p class="person__name">Marcus Delgrove</p>
      <p class="person__role">Store Manager</p>
    </div>

    <span class="divider"></span>

    <ul class="contact">
      <li class="contact__item">
        <svg class="contact__icon" viewBox="0 0 11 11" aria-hidden="true">
          <rect width="11" height="11" fill="#f05a22"/>
          <rect x="3.5" y="1.8" width="4" height="7.4" rx=".8" fill="none" stroke="#fff" stroke-width=".9"/>
        </svg>
        (210) 555-0147
      </li>
      <li class="contact__item">
        <svg class="contact__icon" viewBox="0 0 11 11" aria-hidden="true">
          <rect width="11" height="11" fill="#f05a22"/>
          <rect x="2" y="3" width="7" height="5" fill="none" stroke="#fff" stroke-width=".9"/>
          <path d="M2 3 L5.5 6 L9 3" fill="none" stroke="#fff" stroke-width=".9"/>
        </svg>
        marcus@brightwickclinic.com
      </li>
      <li class="contact__item">
        <svg class="contact__icon" viewBox="0 0 11 11" aria-hidden="true">
          <rect width="11" height="11" fill="#f05a22"/>
          <circle cx="5.5" cy="5.5" r="3.4" fill="none" stroke="#fff" stroke-width=".9"/>
          <path d="M2.1 5.5 H8.9 M5.5 2.1 V8.9" stroke="#fff" stroke-width=".7"/>
        </svg>
        www.brightwickclinic.com
      </li>
    </ul>

    <div class="address-band">4810 E Harlow Ridge Rd, Suite 417, San Antonio, TX 78163</div>
  </section>

  <section class="card card--back" aria-label="Business card back">
    <div class="brand">
      <span class="brand__mark"></span>
      <span class="brand__name">Brightwick Gadget Clinic</span>
    </div>
  </section>
</body>
</html>
```